Lorvex Tilo medical cannibis cultivation company

tag - Tilo rise
Lorvex Tilo medical cannabis cultivation - logo is selected- can we please see bold examples with our selection. We are mainly dealing with medical companies and professionals. We would like to be stand out in the crowd with our designs. Welcome any and all attempts. Thanks

Target Market(s)

Medical and Professional

Industry/Entity Type

Medical And Science

Font styles to use
Sans Serif

Colors

Designer to choose colors to be used in the design.

Requirements
Must have
• Bright colour and be bold- Love the teal and magenta that is currently on the dark background design.
Nice to have
• shading and the 3D affect- The shadowed appearance.
Should not have
• Anything related to illegal activity or un professional manners

```html
<!DOCTYPE html>
<html lang="en">
<head>
<meta charset="utf-8">
<title>Lorvex Tilo — Business Card</title>
<link href="https://fonts.googleapis.com/css2?family=Tenor+Sans&family=Tinos&display=swap" rel="stylesheet">
<style>
  :root {
    --page: #e4e4e4;
    --sky: #00aee8;
    --plum: #9c4a99;
    --paper: #ffffff;
    --slate: #8a9096;
    --ink-light: #ffffff;
  }
  * { margin: 0; padding: 0; box-sizing: border-box; }
  html, body {
    width: 1125px; height: 1200px; overflow: hidden;
    background: var(--page);
  }
  .card {
    position: absolute;
    left: 171px;
    width: 826px; height: 472px;
    border-radius: 26px;
    overflow: hidden;
  }
  .card--front { top: 106px; background: var(--sky); }
  .card--back { top: 639px; background: var(--paper); }

  .front-panel { position: absolute; inset: 0; }

  .contact {
    position: absolute;
    right: 67px; top: 190px;
    text-align: right;
    color: var(--ink-light);
  }
  .contact__name {
    font-family: "Tenor Sans", sans-serif;
    font-size: 31px; letter-spacing: 0.5px; line-height: 34px;
  }
  .contact__role {
    font-family: "Tenor Sans", sans-serif;
    font-size: 20px; font-weight: 700; line-height: 24px;
    margin-bottom: 18px;
  }
  .contact__address {
    font-family: "Tinos", serif;
    font-size: 20px; line-height: 25px;
    margin-bottom: 14px;
  }
  .contact__list { list-style: none; font-family: "Tinos", serif; font-size: 19px; }
  .contact__list li {
    display: flex; justify-content: flex-end; align-items: center;
    gap: 10px; height: 26px;
  }
  .contact__list svg { width: 18px; height: 18px; fill: var(--ink-light); }

  .brand {
    position: absolute; left: 0; right: 0; top: 110px;
    text-align: center;
  }
  .brand__ring {
    display: block; margin: 0 auto 4px;
    width: 176px; height: 176px;
  }
  .brand__name {
    font-family: "Tenor Sans", sans-serif;
    font-size: 50px; line-height: 54px;
    color: var(--plum);
  }
  .brand__tag {
    display: flex; justify-content: center; align-items: center; gap: 8px;
    font-family: "Tenor Sans", sans-serif;
    font-size: 21px; letter-spacing: 2px; text-transform: uppercase;
    color: var(--slate);
  }
  .brand__tag::before, .brand__tag::after {
    content: ""; width: 58px; height: 2px; background: var(--slate);
  }
</style>
</head>
<body>
  <section class="card card--front">
    <svg class="front-panel" viewBox="0 0 826 472" aria-hidden="true">
      <path d="M0 0 H215 C310 120 305 300 150 472 H0 Z" fill="var(--plum)"/>
    </svg>
    <div class="contact">
      <p class="contact__name">MARA VENHOLT</p>
      <p class="contact__role">CEO/FOUNDER</p>
      <p class="contact__address">4120 Fernwick Row<br>Halden Falls, Oregon 97810</p>
      <ul class="contact__list">
        <li>555 218 4096
          <svg viewBox="0 0 24 24"><path d="M6.6 10.8a15 15 0 0 0 6.6 6.6l2.2-2.2a1 1 0 0 1 1-.25 11.4 11.4 0 0 0 3.6.6 1 1 0 0 1 1 1V20a1 1 0 0 1-1 1A17 17 0 0 1 3 4a1 1 0 0 1 1-1h3.5a1 1 0 0 1 1 1c0 1.25.2 2.45.6 3.6a1 1 0 0 1-.25 1z"/></svg>
        </li>
        <li>mara@lorvextilo.com
          <svg viewBox="0 0 24 24"><path d="M2 5h20v14H2z M3 6l9 7 9-7" fill="var(--ink-light)" stroke="var(--sky)" stroke-width="1.5"/></svg>
        </li>
        <li>www.lorvextilo.com
          <svg viewBox="0 0 24 24"><circle cx="12" cy="12" r="10"/><path d="M8 6c3 1 2 4 5 5s1 5-1 7M16 5c-1 2 1 3 3 4" fill="none" stroke="var(--sky)" stroke-width="2"/></svg>
        </li>
      </ul>
    </div>
  </section>

  <section class="card card--back">
    <div class="brand">
      <svg class="brand__ring" viewBox="0 0 176 176" aria-hidden="true">
        <circle cx="88" cy="88" r="84" fill="none" stroke="var(--slate)" stroke-width="5"/>
      </svg>
      <p class="brand__name">LORVEX TILO</p>
      <p class="brand__tag">Tilo rise</p>
    </div>
  </section>
</body>
</html>
```